ULMIRA card Technical Architecture

Hello everyone ULMIRA: It is a consulting firm in Architecture and Construction. I require a card duplexing, sober, elegant, classic but not boring. Update 1: Use the following data for the card. Name: Gonzalo Pereda Mauricio Villalta Position: COO Twitter: @ulmiraAT Homepage: ulmira-example.com home address not include the participation of all thank you.

Target Market(s)

Construction companies, Architects and Consulting Engineers

Industry/Entity Type

Consulting

Contact Information for Business Card

Los campos que debe tener:
Nombre, Cargo, email, homepage y twitter

Font styles to use
Serif
Sans Serif
Other font styles liked:
• Me gustan playfair display, open sans y roboto, pero estoy sujeto a sus propuestas

Requirements
Must have
• Colors: Present combined proposals in white, red, gray and black Update 1: The two names must be clearly differentiated from the two surnames
Nice to have
• They are free to present their best proposals. I will bring them immediate feedback to the extent you can go see their designs. Complete data for card and logo files will give the winner the

```html
<!DOCTYPE html>
<html lang="es">
<head>
<meta charset="utf-8">
<title>ULMIRA – Tarjeta de presentación</title>
<link rel="stylesheet" href="https://fonts.googleapis.com/css2?family=Montserrat:wght@400;500;700&display=swap">
<style>
  :root {
    --stage: #2b2b2b;
    --card-dark: #2a2a2a;
    --card-light: #ffffff;
    --ink: #1c1c1c;
    --wine: #6d1016;
    --red: #a8141c;
    --grey: #9a9a9a;
    --white: #ffffff;
  }
  * { box-sizing: border-box; margin: 0; padding: 0; }
  html, body {
    width: 1200px; height: 900px; overflow: hidden;
    background: var(--stage);
    font-family: "Montserrat", sans-serif;
  }
  .stage {
    width: 1200px; height: 900px;
    display: flex; flex-direction: column;
    align-items: center; justify-content: center; gap: 56px;
  }
  .card {
    width: 630px; height: 360px;
    border-radius: 22px;
    position: relative;
    box-shadow: 0 14px 30px rgba(0,0,0,.45);
  }
  /* Back side */
  .card--back {
    background: var(--card-dark);
    color: var(--white);
    display: flex; flex-direction: column;
    align-items: center; justify-content: center;
  }
  .brand-back {
    display: flex; align-items: center; gap: 14px;
    font-weight: 500; font-size: 46px; letter-spacing: 10px;
    color: var(--white);
  }
  .brand-back .mark {
    width: 16px; height: 16px; border-radius: 50%;
    background: var(--white);
  }
  .social-handle {
    position: absolute; bottom: 58px; left: 0; right: 0;
    display: flex; justify-content: center; align-items: center; gap: 8px;
    font-size: 14px; color: var(--white);
  }
  .social-handle .dot {
    width: 10px; height: 10px; border-radius: 50%; background: var(--white);
  }
  /* Front side */
  .card--front {
    background: var(--card-light);
    color: var(--ink);
    display: flex; align-items: center;
    padding: 0 44px 0 60px;
  }
  .brand-front {
    width: 285px;
    display: flex; align-items: center; gap: 12px;
    font-weight: 500; font-size: 44px; letter-spacing: 9px;
    color: var(--ink);
  }
  .brand-front .mark {
    width: 14px; height: 14px; background: var(--red);
  }
  .contact { flex: 1; padding-left: 20px; }
  .person-first, .person-last {
    font-weight: 700; font-size: 23px; color: var(--wine); line-height: 1.1;
  }
  .role {
    font-size: 13px; color: var(--ink); margin: 3px 0 8px;
  }
  .details { list-style: none; margin-top: 6px; }
  .details li {
    display: flex; align-items: center; gap: 9px;
    font-size: 13px; line-height: 1.55; color: var(--ink);
  }
  .details svg { width: 11px; height: 11px; flex: none; }
</style>
</head>
<body>
  <main class="stage">
    <section class="card card--back" aria-label="Reverso de la tarjeta">
      <div class="brand-back"><span class="mark"></span>ULMIRA</div>
      <p class="social-handle"><span class="dot"></span>@ulmiraAT</p>
    </section>

    <section class="card card--front" aria-label="Anverso de la tarjeta">
      <div class="brand-front"><span class="mark"></span>ULMIRA</div>
      <div class="contact">
        <h1 class="person-first">Mauricio Gonzalo</h1>
        <p class="role">COO</p>
        <h2 class="person-last">Pereda Villalta</h2>
        <p class="role">Director de Operaciones</p>
        <ul class="details">
          <li>
            <svg viewBox="0 0 12 12" aria-hidden="true"><path d="M2.5 1 L4.5 1 L5.2 3.6 L4 4.6 Q5 7 7.4 8 L8.4 6.8 L11 7.5 L11 9.5 Q10.5 11 9 11 Q1 10 1 2.8 Q1 1.2 2.5 1 Z" fill="var(--red)"/></svg>
            (+571) 555 010 2030
          </li>
          <li>
            <svg viewBox="0 0 12 12" aria-hidden="true"><rect x="1" y="2.5" width="10" height="7" rx="1" fill="var(--red)"/><path d="M1.5 3 L6 6.5 L10.5 3" stroke="#fff" stroke-width="1" fill="none"/></svg>
            info@ulmira-example.com
          </li>
          <li>
            <svg viewBox="0 0 12 12" aria-hidden="true"><circle cx="6" cy="6" r="5" fill="var(--red)"/><path d="M1 6 H11 M6 1 Q3 6 6 11 M6 1 Q9 6 6 11" stroke="#fff" stroke-width=".8" fill="none"/></svg>
            www.ulmira-example.com
          </li>
        </ul>
      </div>
    </section>
  </main>
</body>
</html>
```